Kelvaro.ch is looking for business card letterhead and envelope C5 with WOW effect

We need a strong business card for our company Kelvaro.ch, logo is available. You want a black or dark background on which the logo Stark r% 26 # 252; appears. Letterhead and envelope in C5 format should be in a similar design, but does not have to be We need a strong business card for our company Kelvaro.ch, logo is available. A black or dark background is desired, on which the logo Stark comes across. The letterhead and the envelope in C5 format should have a similar design.

Target Market(s)

Private customers as well as entrepreneurs

Contact Information for Business Card

E-mail: info@kelvaro-example.ch
Web.www.Kelvaro-example.ch
Tel: +41 ( 0 ) 79 482 6037
Adresse:
Lindenweg 14
9406 Tarnbach

Hier kann man Icons verwenden für Email,Tel und Adressse

Font styles to use
Other font styles liked:
• Dubai,bold

Colors

Designer to choose colors to be used in the design.

Requirements
Must have
• WOW effect
Nice to have
• R% 26 # 252; back business card with our service listings. - VEHICLE LABELING - SHOP WINDOW LABELING - STICKERS AND MUCH MORE ... in red color

```html
<!DOCTYPE html>
<html lang="en">
<head>
<meta charset="utf-8">
<title>Kelvaro.ch – Business Card</title>
<link rel="stylesheet" href="https://fonts.googleapis.com/css2?family=Open+Sans:wght@400;600;700&display=swap">
<style>
  :root {
    --stage: #1a1a1a;
    --card: #1f1f1f;
    --card-edge: #2a2a2a;
    --white: #ffffff;
    --soft-white: #e9e9e9;
    --yellow: #f7c600;
    --red: #e0232a;
  }
  * { box-sizing: border-box; margin: 0; padding: 0; }
  html, body {
    width: 1200px; height: 900px; overflow: hidden;
    background: var(--stage);
    font-family: "Open Sans", Arial, sans-serif;
    color: var(--white);
  }
  .stage {
    position: relative; width: 1200px; height: 900px;
    display: flex; flex-direction: column; align-items: center; justify-content: center; gap: 48px;
  }
  .card {
    position: relative; width: 640px; height: 366px;
    background: linear-gradient(135deg, var(--card) 0%, var(--card-edge) 70%, var(--card) 100%);
    box-shadow: 0 14px 30px rgba(0,0,0,.55);
  }
  .brand {
    display: flex; align-items: center; gap: 16px;
  }
  .brand-dot {
    width: 46px; height: 46px; border-radius: 50%; background: var(--yellow);
  }
  .brand-name {
    font-weight: 700; font-size: 38px; color: var(--white); letter-spacing: 1px;
  }
  /* front */
  .card-front .brand { position: absolute; left: 170px; top: 110px; }
  .services {
    position: absolute; right: 160px; top: 206px; list-style: none; text-align: right;
    font-size: 15px; line-height: 22px; color: var(--soft-white); text-transform: uppercase;
  }
  .services li { display: flex; align-items: center; justify-content: flex-end; gap: 10px; }
  .services li::after {
    content: ""; width: 8px; height: 8px; border: 2px solid var(--red); border-radius: 50%;
  }
  /* back */
  .card-back .brand { position: absolute; left: 56px; top: 150px; }
  .card-back .brand-name { font-size: 32px; }
  .card-back .brand-dot { width: 40px; height: 40px; }
  .divider {
    position: absolute; left: 352px; top: 96px; width: 2px; height: 176px; background: var(--yellow);
  }
  .contact { position: absolute; left: 382px; top: 90px; }
  .person-name { font-weight: 700; font-size: 22px; text-transform: uppercase; letter-spacing: .5px; }
  .person-name .surname { color: var(--yellow); }
  .person-role { font-size: 16px; color: var(--soft-white); letter-spacing: 1px; margin-bottom: 14px; }
  .address { font-size: 17px; line-height: 24px; letter-spacing: 1px; color: var(--soft-white); margin-bottom: 6px; }
  .contact-list { list-style: none; font-size: 17px; line-height: 26px; letter-spacing: .8px; color: var(--soft-white); }
  .contact-list li { display: flex; align-items: center; gap: 10px; }
  .contact-list svg { width: 16px; height: 16px; flex: none; }
</style>
</head>
<body>
<main class="stage">
  <section class="card card-front">
    <div class="brand">
      <span class="brand-dot"></span>
      <span class="brand-name">Kelvaro.ch</span>
    </div>
    <ul class="services">
      <li>Vehicle labeling</li>
      <li>Shop window labeling</li>
      <li>Stickers and much more</li>
    </ul>
  </section>

  <section class="card card-back">
    <div class="brand">
      <span class="brand-dot"></span>
      <span class="brand-name">Kelvaro.ch</span>
    </div>
    <span class="divider"></span>
    <div class="contact">
      <p class="person-name">Lukas <span class="surname">Brenner</span></p>
      <p class="person-role">Director</p>
      <p class="address">Lindenweg 14<br>9406 Tarnbach</p>
      <ul class="contact-list">
        <li>
          <svg viewBox="0 0 16 16" aria-hidden="true"><path d="M4 1.5l2.2 3-1.3 1.5c.8 1.9 2.2 3.4 4.1 4.3l1.5-1.3 3 2.2-1.2 2.6C7 13.6 2.4 9 1.7 2.7z" fill="none" stroke="var(--yellow)" stroke-width="1.4" stroke-linejoin="round"/></svg>
          +41(0)79 482 6037
        </li>
        <li>
          <svg viewBox="0 0 16 16" aria-hidden="true"><rect x="1.5" y="3.5" width="13" height="9" fill="none" stroke="var(--yellow)" stroke-width="1.4"/><path d="M1.5 3.5l6.5 5 6.5-5" fill="none" stroke="var(--yellow)" stroke-width="1.4"/></svg>
          info@kelvaro-example.ch
        </li>
        <li>
          <svg viewBox="0 0 16 16" aria-hidden="true"><g fill="none" stroke="var(--yellow)" stroke-width="1.3"><circle cx="8" cy="8" r="6.5"/><ellipse cx="8" cy="8" rx="2.8" ry="6.5"/><path d="M1.5 8h13M2.5 4.8h11M2.5 11.2h11"/></g></svg>
          www.kelvaro-example.ch
        </li>
      </ul>
    </div>
  </section>
</main>
</body>
</html>
```